Designing a website that functions as the shop window for the various aspects of my business -...

I need a website, with separate webpages covering the different components of my practice (small animal consultancy, equine behaviour consultancy, legal case work and education provider). I have a website (www.petcalmstudio.ie) but I haven't updated it in recent years to reflect the newer developments / aspects of my business. Most of my work has been in Ireland but I would like to begin to create an international profile, particularly with regard to the legal casework and offering education within the international horse industry. My overall goal is to improve understanding of animals and animal behaviour, and by doing so, help to reduce the performance of behaviour problems, and also improve animal welfare as a result.

Target Market(s)

Horse and dog owners, horse riders, veterinary surgeons, solicitors

Industry/Entity Type

Legal

Logo Text

Text to be decided on

Number of Pages Required

5+ page

Font styles to use
Sans Serif
Decorative
Script

Colors

Designer to choose colors to be used in the design.

Requirements
Must have
• Relevant content from the attached Flyer including photos
• Use of the phrases:
• 'Understanding Animals'
• Improving animals lives through better understanding
• Science-based, up-to-date relevant information regarding animal behaviour
Nice to have
• 'Leading professional service educating people in understanding animals'
• Separate pages for 1) About, 2) Canine and Feline behaviour Consultancy 3) Equine Consultancy 4) Legal expert witness Consultancy 5) Education 6, FAQs
Should not have
• Prices of services (as these may change from time to time)

```html
<!DOCTYPE html>
<html lang="en">
<head>
<meta charset="utf-8">
<title>PetCalm Studio</title>
<link href="https://fonts.googleapis.com/css2?family=Lato:wght@400;700;900&family=Roboto:wght@400;500;700&display=swap" rel="stylesheet">
<style>
:root{
  --green:#128a45;
  --green-dark:#0c6b34;
  --ink:#1a1a1a;
  --text:#555;
  --dark:#1c1c1c;
  --white:#fff;
  --soft:#f3f5f4;
}
*{margin:0;padding:0;box-sizing:border-box}
html,body{width:1200px;height:4147px;overflow:hidden}
body{font-family:Roboto,Arial,sans-serif;color:var(--text);background:var(--white);position:relative}
.abs{position:absolute}
h1,h2,h3,h4{font-family:Lato,Arial,sans-serif;color:var(--ink)}

/* header */
.site-header{top:0;left:0;width:1200px;height:140px;background:var(--white)}
.brand{left:0;width:1200px;top:28px;display:flex;justify-content:center;align-items:center;gap:14px}
.brand-dot{width:34px;height:34px;border-radius:50%;background:var(--green)}
.brand-name{font-family:Lato,sans-serif;font-weight:700;font-size:34px;color:var(--green)}
.main-nav{left:95px;top:118px;width:1010px;height:40px;background:#222;display:flex;align-items:center;padding-left:35px;gap:30px;z-index:3}
.main-nav::before,.main-nav::after{content:"";position:absolute;top:0;width:24px;height:40px;background:var(--green)}
.main-nav::before{left:-14px;transform:skewX(25deg)}
.main-nav::after{right:-14px;transform:skewX(-25deg)}
.main-nav a{color:var(--white);text-decoration:none;font-family:Roboto,sans-serif;font-weight:500;font-size:15px;text-transform:uppercase}
.main-nav .contact{margin-left:auto;margin-right:35px}

/* hero */
.hero{top:140px;left:0;width:1200px;height:600px;background:linear-gradient(180deg,#5d7b48 0%,#46692f 45%,#5b8a32 100%)}
.hero-text{left:645px;top:330px;width:500px}
.hero-text h2{color:var(--white);font-size:40px;font-weight:900}
.hero-text p{color:var(--white);font-size:17px;line-height:1.55;margin-top:14px}
.btn{display:inline-block;background:var(--green);color:var(--white);font-weight:700;font-size:15px;padding:13px 30px;border-radius:24px;text-transform:uppercase}
.btn-outline{display:inline-block;background:var(--white);color:var(--green);font-weight:700;font-size:14px;padding:12px 26px;border-radius:24px;border:2px solid var(--green);text-transform:uppercase}
.hero-text .btn{margin-top:30px}
.arrow{top:395px;color:var(--white);font-size:30px}
.hero-curve{top:600px;left:0}

/* welcome */
.welcome{top:790px;left:0;width:1200px;text-align:center}
.welcome h2{font-size:44px;font-weight:900}
.welcome p{width:860px;margin:32px auto 0;font-size:15px;line-height:1.85}
.welcome p + p{margin-top:26px}
.green-block{left:0;top:1217px;width:373px;height:318px;background:var(--green)}
.video{left:199px;top:1114px;width:382px;height:304px;background:linear-gradient(135deg,#3a3f55,#1a1c22 60%,#4a3a2a)}
.play{left:362px;top:1250px;width:56px;height:38px;border-radius:10px;background:#e0241f}
.play::after{content:"";position:absolute;left:21px;top:11px;border-left:16px solid #fff;border-top:8px solid transparent;border-bottom:8px solid transparent}
.consult{left:644px;top:1114px;width:440px}
.consult h3{font-size:31px;font-weight:700;letter-spacing:1px;line-height:1.25;border-left:5px solid var(--green);padding-left:20px;text-transform:uppercase}
.consult ul{list-style:none;margin-top:22px}
.consult li{display:flex;gap:12px;font-size:15px;line-height:1.5;margin-bottom:18px}
.consult li svg{flex:none;margin-top:2px}
.consult .btn-outline{margin-top:10px}

/* components */
.components{top:1535px;left:0;width:1200px;height:649px;background:linear-gradient(180deg,#3e3a33,#56503f 55%,#2d3b20)}
.components h2{position:absolute;top:130px;width:1200px;text-align:center;color:var(--white);font-size:44px;font-weight:900}
.comp{width:262px;height:262px;border-radius:50%;border:6px solid var(--green);box-shadow:0 0 0 4px #fff inset;display:flex;flex-direction:column;justify-content:flex-end;align-items:center;text-align:center;padding-bottom:52px;color:var(--white);font-family:Lato,sans-serif;font-weight:700;font-size:18px;text-transform:uppercase}
.comp.a{left:112px;top:1805px;background:linear-gradient(160deg,#8c8f77,#474a3a)}
.comp.b{left:472px;top:1805px;background:rgba(30,30,30,.72);justify-content:center;padding:0 30px}
.comp.c{left:828px;top:1805px;background:linear-gradient(160deg,#6a4a33,#2f3a22)}
.comp.b small{display:block;font-family:Roboto,sans-serif;text-transform:none;font-weight:400;font-size:14px;margin-top:12px;line-height:1.5}
.comp.b i{display:block;margin:12px auto 0;width:24px;height:24px;border-radius:50%;background:#fff}

/* specialized */
.special{top:2184px;left:0;width:1200px;height:788px;background:var(--soft)}
.we-are{top:2286px;left:0;width:1200px;text-align:center;font-family:Lato,sans-serif;font-size:28px;color:var(--ink)}
.special-title{top:2326px;left:0;width:1200px;text-align:center;font-size:46px;font-weight:900}
.card{width:298px;background:var(--white);box-shadow:0 2px 12px rgba(0,0,0,.12);text-align:center;padding-bottom:24px}
.card .photo{height:196px}
.card .badge{width:64px;height:64px;border-radius:50%;background:var(--white);margin:-34px auto 0;position:relative;display:flex;align-items:center;justify-content:center}
.card .badge span{width:34px;height:34px;border-radius:50%;background:var(--green)}
.card h4{font-size:21px;font-weight:700;margin-top:14px;text-transform:uppercase}
.card p{font-size:14px;line-height:1.6;margin:16px 28px 0}
.card .btn-outline,.card .btn{margin-top:18px;font-size:13px;padding:8px 20px}
.card.dogs{left:111px;top:2372px}
.card.horses{left:451px;top:2439px}
.card.cats{left:794px;top:2372px}

/* news */
.news-block{left:826px;top:2972px;width:374px;height:318px;background:var(--green)}
.news h2{font-size:44px;font-weight:900;text-transform:uppercase}
.news{left:111px;top:3100px;width:420px}
.news-item{margin-top:40px}
.news-item time{font-size:14px;color:var(--ink)}
.news-item h4{font-family:Roboto,sans-serif;font-size:23px;font-weight:500;line-height:1.45;margin-top:10px}
.news-item a{display:inline-block;margin-top:16px;font-size:15px;color:var(--ink);border-bottom:2px solid var(--green);padding-bottom:3px;text-decoration:none}
.news-feature{left:603px;top:3116px;width:484px;height:387px;background:linear-gradient(160deg,#c7a27a,#7a5538 60%,#2d2a25)}
.news-feature .cap{position:absolute;left:46px;bottom:32px;color:var(--white)}
.news-feature time{font-size:14px}
.news-feature h4{color:var(--white);font-family:Roboto,sans-serif;font-weight:500;font-size:22px;line-height:1.45;margin-top:8px}

/* footer */
.footer-curve{top:3480px;left:0}
.footer{top:3705px;left:0;width:1200px;height:442px;background:var(--dark)}
.social{left:111px;top:3800px;display:flex;gap:16px}
.social span{width:22px;height:22px;border-radius:50%;background:var(--white)}
.foot-links{left:111px;top:3870px;list-style:none;color:var(--white);font-size:15px}
.foot-links li{margin-bottom:6px}
.foot-links li::before{content:"\00BB";margin-right:14px}
.foot-col h4{color:var(--white);font-family:Roboto,sans-serif;font-size:16px;font-weight:700;text-transform:uppercase}
.newsletter{left:456px;top:3800px;width:280px;text-align:center}
.newsletter p{color:var(--white);font-size:14px;line-height:1.6;margin-top:32px}
.newsletter .field{margin-top:22px;height:42px;border:2px solid var(--green);color:#ccc;font-size:13px;line-height:38px}
.newsletter .submit{margin-top:12px;height:42px;background:var(--green);color:var(--white);font-weight:700;font-size:15px;line-height:42px;text-transform:uppercase}
.contact-info{left:808px;top:3800px;width:300px}
.contact-info h4::after{content:"";display:block;width:60px;height:2px;background:var(--green);margin-top:16px}
.contact-info ul{list-style:none;margin-top:28px;color:var(--white);font-size:14px;line-height:1.5}
.contact-info li{display:flex;gap:18px;margin-bottom:22px}
.contact-info li svg{flex:none;margin-top:2px}
.copyright{top:4087px;left:0;width:1200px;text-align:center;color:var(--white);font-size:15px}
</style>
</head>
<body>

<header class="site-header abs">
  <div class="brand abs"><span class="brand-dot"></span><span class="brand-name">PetCalm Studio</span></div>
</header>
<nav class="main-nav abs">
  <a href="#">Home</a><a href="#">About</a><a href="#">Canine &amp; Feline Behaviour Consultancy</a><a href="#">Equine Consultancy</a><a href="#">More ▾</a><a class="contact" href="#">Contact Us</a>
</nav>

<section class="hero abs" role="img" aria-label="Photo of a collie dog running across a green lawn"></section>
<div class="arrow abs" style="left:14px">‹</div>
<div class="arrow abs" style="right:14px">›</div>
<div class="hero-text abs">
  <h2>Behaviour Of Your Pet</h2>
  <p>Lorem ipsum dolor sit amet consectetur adipiscing elit sed eiusmod tempor incididunt labore.</p>
  <span class="btn">Read More ➜</span>
</div>
<svg class="hero-curve abs" width="1200" height="260" viewBox="0 0 1200 260">
  <path d="M0 260 L0 240 C150 80 450 40 1200 60 L1200 260 Z" fill="#fff"/>
  <path d="M0 240 C150 80 450 40 1200 60" fill="none" stroke="#128a45" stroke-width="6"/>
</svg>

<section class="welcome abs">
  <h2>WELCOME TO OUR CLINIC</h2>
  <p>Animals have been used by humans for a variety of purposes, including as a source of food, for hunting, for mobility, to help win battles, for sport - and most recently, for companionship.</p>
  <p>Whether we are dog or cat lovers, horseriders or owners, through the course of our relationship with our animals, many of us will be faced with problem behaviours, such as aggression, excessive barking, destructiveness (dogs), spraying, fear problems, aggression (cats), bucking, refusing to load into trailers, rearing, shying (horses).</p>
</section>

<div class="green-block abs"></div>
<div class="video abs" role="img" aria-label="Video still of a talk given to an audience"></div>
<div class="play abs"></div>
<div class="consult abs">
  <h3>Canine and Feline Consultations</h3>
  <ul>
    <li><svg width="20" height="20" viewBox="0 0 20 20"><circle cx="10" cy="10" r="8.5" fill="none" stroke="#777" stroke-width="1.5"/><path d="M6 10l3 3 5-6" fill="none" stroke="#777" stroke-width="1.6"/></svg>Understanding Animals</li>
    <li><svg width="20" height="20" viewBox="0 0 20 20"><circle cx="10" cy="10" r="8.5" fill="none" stroke="#777" stroke-width="1.5"/><path d="M6 10l3 3 5-6" fill="none" stroke="#777" stroke-width="1.6"/></svg>Improving animals lives through better understanding</li>
    <li><svg width="20" height="20" viewBox="0 0 20 20"><circle cx="10" cy="10" r="8.5" fill="none" stroke="#777" stroke-width="1.5"/><path d="M6 10l3 3 5-6" fill="none" stroke="#777" stroke-width="1.6"/></svg>Science-based, up-to-date relevant information regarding animal behaviour</li>
  </ul>
  <span class="btn-outline">Get a Consultation ➜</span>
</div>

<section class="components abs" role="img" aria-label="Photo of a golden retriever in a field at sunset">
  <h2>COMPONENTS OF MY PRACTICE</h2>
</section>
<div class="comp a abs" role="img" aria-label="Photo of a puppy and kitten">Small Animal<br>Consultancy</div>
<div class="comp b abs">Equine Behaviour Consultancy<small>We encourage owners to attend our clinics with their dog</small><i></i></div>
<div class="comp c abs" role="img" aria-label="Photo of a rider with a horse">Legal Case<br>Work</div>

<section class="special abs"></section>
<div class="we-are abs">WE ARE</div>
<h2 class="special-title abs">SPECIALIZED</h2>
<article class="card dogs abs">
  <div class="photo" role="img" aria-label="Photo of a dog lying on a rug" style="background:linear-gradient(160deg,#d8d2c8,#a4653a)"></div>
  <div class="badge"><span></span></div>
  <h4>Dogs Behaviour</h4>
  <p>Sed ut perspiciatis unde omnis natus error sit voluptatem accusantium doloremque laudantium totam rem</p>
  <span class="btn-outline">Read More ➜</span>
</article>
<article class="card horses abs">
  <div class="photo" role="img" aria-label="Photo of a woman with a horse in sunlight" style="background:linear-gradient(160deg,#e6b04a,#6b4a22)"></div>
  <div class="badge"><span></span></div>
  <h4>Horses Behaviour</h4>
  <p>Sed ut perspiciatis unde omnis natus error sit voluptatem accusantium doloremque laudantium totam rem</p>
  <span class="btn">Read More ➜</span>
</article>
<article class="card cats abs">
  <div class="photo" role="img" aria-label="Photo of a cat held in knitted sleeves" style="background:linear-gradient(160deg,#e8ddd2,#b58d6a)"></div>
  <div class="badge"><span></span></div>
  <h4>Cats Behaviour</h4>
  <p>Sed ut perspiciatis unde omnis natus error sit voluptatem accusantium doloremque laudantium totam rem</p>
  <span class="btn-outline">Read More ➜</span>
</article>

<div class="news-block abs"></div>
<section class="news abs">
  <h2>LATEST NEWS</h2>
  <div class="news-item"><time>Mar 23, 2018</time><h4>Lorem ipsum dolor sit amet consect etur adipiscing sed eiusmod.</h4><a href="#">Read More ➜</a></div>
  <div class="news-item"><time>Mar 23, 2018</time><h4>Lorem ipsum dolor sit amet consect etur adipiscing sed eiusmod.</h4><a href="#">Read More ➜</a></div>
</section>
<div class="news-feature abs" role="img" aria-label="Photo of a small dog giving a high five">
  <div class="cap"><time>Mar 23, 2018</time><h4>Sed ut perspiciatis unde omnis iste<br>natus error sit voluptatem...</h4></div>
</div>

<svg class="footer-curve abs" width="1200" height="230" viewBox="0 0 1200 230">
  <path d="M0 230 L0 190 C500 230 950 160 1200 0 L1200 230 Z" fill="#1c1c1c"/>
  <path d="M0 190 C500 230 950 160 1200 0" fill="none" stroke="#128a45" stroke-width="6"/>
</svg>
<footer class="footer abs"></footer>
<div class="social abs"><span></span><span></span><span></span><span></span><span></span></div>
<ul class="foot-links abs">
  <li>Home</li><li>About Us</li><li>Equine Consultancy</li><li>Education,</li><li>Legal expert witness Consultancy</li><li>Contact Us</li>
</ul>
<div class="newsletter foot-col abs">
  <h4>Newsletter Subscription</h4>
  <p>Register your Email Address to get a more Information about us</p>
  <div class="field">Email Address *</div>
  <div class="submit">Subscribe</div>
</div>
<div class="contact-info foot-col abs">
  <h4>Contact Information</h4>
  <ul>
    <li><svg width="16" height="20" viewBox="0 0 16 20"><path d="M8 0a7 7 0 0 0-7 7c0 5 7 13 7 13s7-8 7-13a7 7 0 0 0-7-7z" fill="#fff"/><circle cx="8" cy="7" r="2.5" fill="#1c1c1c"/></svg>123 Sample Street, Sample City, Sample State, USA.</li>
    <li><svg width="16" height="16" viewBox="0 0 16 16"><path d="M3 1l3 3-2 2c1 2 3 4 5 5l2-2 3 3-2 3C6 15 1 10 0 4z" fill="#fff"/></svg>555 019 4820</li>
    <li><svg width="16" height="14" viewBox="0 0 16 14"><rect x="0" y="1" width="16" height="12" fill="#fff"/><path d="M0 1l8 6 8-6" fill="none" stroke="#1c1c1c" stroke-width="1.4"/></svg>hello@petcalmstudio.ie</li>
  </ul>
</div>
<div class="copyright abs">Copyrights © 2019 PetCalm Studio. All Rights Reserved &nbsp;&nbsp;|&nbsp;&nbsp; Privacy Policy.</div>

</body>
</html>
```